Stationery Design Project for Nimbora, Chicago

Nimbora, a street parking application which helps car drivers find a street parking spot by offering an ideal path along which to look for parking. This path is calculated by our algorithm based on data (e.g. historical data, baseball games schedule, etc.). Along this path the driver will find a spot and will also save 70% of the search time. Customer we target is reg. between 21 and 45 yo.

We envision something young, fresh, bright and original. Slightly abstract maybe. It should represent the idea and elements of finding street parking in the city, e.g. car(s), parking spot, people, city, etc. (just ideas!).

Logo is attached.

Requirement:
- Business Cards (2 Sided Full Color CMYK)
- Letterhead (1 Sided Full Color CMYK)
- Envelope (1 Sided Full Color CMYK)
- Sticker (1 Sided Full Color CMYK), round with a 2inch diameter.

Reason: We're starting to get more and more designs and need more time to look into all of them. Very exciting!! Thanks to everybody!

Hi all, we're in the process of selecting our favs. Though choices!!! Really good submissions. Will keep you posted and sorry for the delay.

Target Market(s)

Car drivers and owners between 21 and 45

Industry/Entity Type

Parking

Requirements
Must have
• Sticker should be round and include company URL nimbora.com and the new logo which we will attach soon.
Should not have
• Should not be too serious or boring.

```html
<!DOCTYPE html>
<html lang="en">
<head>
<meta charset="utf-8">
<title>Nimbora Business Cards</title>
<link href="https://fonts.googleapis.com/css2?family=Open+Sans:wght@400;600&display=swap" rel="stylesheet">
<style>
  :root {
    --canvas-bg: #ececec;
    --card-bg: #ffffff;
    --ink: #2b2b2b;
    --wordmark: #333333;
    --accent-cyan: #2a9fd8;
    --band-grey: #4a4a4c;
    --blue-deep: #233f96;
    --blue-bright: #3b66cc;
    --mark-blue: #1f5fd6;
    --white: #ffffff;
  }
  * { margin: 0; padding: 0; box-sizing: border-box; }
  html, body {
    width: 1200px; height: 1063px; overflow: hidden;
    background: var(--canvas-bg);
    font-family: "Open Sans", Arial, sans-serif;
  }
  .canvas { position: relative; width: 1200px; height: 1063px; }
  .card {
    position: absolute; width: 764px; height: 436px;
    background: var(--card-bg);
    box-shadow: 0 2px 10px rgba(0,0,0,0.18);
    overflow: hidden;
  }
  .card--front { left: 70px; top: 80px; }
  .card--back { left: 351px; top: 549px; }
  .card__swoosh { position: absolute; inset: 0; }
  .brand { position: absolute; display: flex; align-items: center; gap: 24px; }
  .brand__dot {
    width: 132px; height: 132px; border-radius: 50%;
    background: var(--mark-blue); flex: none;
  }
  .brand__name {
    font-size: 84px; font-weight: 600; color: var(--wordmark);
    letter-spacing: -1px; line-height: 1;
  }
  .card--front .brand { left: 50px; top: 40px; }
  .card--back .brand { left: 147px; top: 135px; }
  .person { position: absolute; left: 47px; top: 272px; color: var(--accent-cyan); }
  .person__name { font-size: 27px; font-weight: 600; }
  .person__title { font-size: 22px; font-weight: 400; }
  .address {
    position: absolute; left: 47px; top: 340px;
    font-size: 18px; line-height: 28px; color: var(--ink);
  }
  .contacts {
    position: absolute; right: 22px; top: 291px;
    list-style: none; color: var(--white); font-size: 18px;
  }
  .contacts__item {
    display: flex; justify-content: flex-end; align-items: center;
    gap: 8px; height: 28px;
  }
  .contacts__icon { width: 16px; height: 16px; flex: none; }
  .website {
    position: absolute; left: 0; right: 0; top: 326px;
    text-align: center; font-size: 24px; letter-spacing: 2px; color: var(--ink);
  }
</style>
</head>
<body>
<main class="canvas">
  <section class="card card--front" aria-label="Business card front">
    <svg class="card__swoosh" width="764" height="436" viewBox="0 0 764 436" aria-hidden="true">
      <defs>
        <linearGradient id="band-blue" x1="0" y1="1" x2="1" y2="0">
          <stop offset="0" stop-color="var(--blue-deep)"/>
          <stop offset="1" stop-color="var(--blue-bright)"/>
        </linearGradient>
      </defs>
      <path d="M228 436 C460 396 610 250 662 0 L764 0 L764 436 Z" fill="var(--band-grey)"/>
      <path d="M285 436 C520 392 690 230 764 42 L764 436 Z" fill="url(#band-blue)"/>
    </svg>
    <div class="brand">
      <span class="brand__dot"></span>
      <span class="brand__name">nimbora</span>
    </div>
    <p class="person"><span class="person__name">Your Name ,</span> <span class="person__title">Title</span></p>
    <p class="address">Complex Name, Street Name<br>Area, City Name,000 000</p>
    <ul class="contacts">
      <li class="contacts__item">+1 312 555 0147
        <svg class="contacts__icon" viewBox="0 0 16 16" aria-hidden="true"><circle cx="8" cy="8" r="7.5" fill="#fff"/><path d="M5 4 L7 4 L7.5 6 L6.5 7 Q7.5 9 9 9.5 L10 8.5 L12 9 L12 11 Q7 12 5 4Z" fill="var(--blue-deep)"/></svg>
      </li>
      <li class="contacts__item">+1 312 555 0147
        <svg class="contacts__icon" viewBox="0 0 16 16" aria-hidden="true"><rect x="4" y="1" width="8" height="14" rx="1.5" fill="#fff"/><rect x="5.5" y="3" width="5" height="6" fill="var(--blue-deep)"/></svg>
      </li>
      <li class="contacts__item">info@nimbora.com
        <svg class="contacts__icon" viewBox="0 0 16 16" aria-hidden="true"><rect x="1" y="3" width="14" height="10" rx="1" fill="#fff"/><path d="M1.5 3.5 L8 9 L14.5 3.5" stroke="var(--blue-deep)" stroke-width="1.3" fill="none"/></svg>
      </li>
      <li class="contacts__item">www.nimbora.com
        <svg class="contacts__icon" viewBox="0 0 16 16" aria-hidden="true"><circle cx="8" cy="8" r="7" fill="#fff"/><path d="M1 8 H15 M8 1 Q4 8 8 15 M8 1 Q12 8 8 15" stroke="var(--blue-deep)" stroke-width="1" fill="none"/></svg>
      </li>
    </ul>
  </section>

  <section class="card card--back" aria-label="Business card back">
    <div class="brand">
      <span class="brand__dot"></span>
      <span class="brand__name">nimbora</span>
    </div>
    <p class="website">www.nimbora.com</p>
  </section>
</main>
</body>
</html>
```